Looking for a website that shows the services available to customers.This company will provide consulting on how to reduce costs and improve overal IT spend within any organization. We will employ experts in many aspects of IT including Cloud, Mainframe, ZR720/oFrame/TFrame, Disaster Recovery, IT optimization strategies, Colocation, Hybrid IT, Migrations, Networking, Security etc. I am a technology advisor that helps to optimize costs in IT

Target Market(s)

Al companies over $1M in revenue

Industry/Entity Type

It Company

Number of Pages Required

5+ page

Font styles to use
Serif
Sans Serif

Requirements
Must have
• Tabs for: About us (our team), Services, Why Solvanta, Testimonials, Contact Us
Nice to have
• i would like to have on my services pages some logos of partners. Such as quellbyte, K&L, etc.

I need an understanding of how to add/change to the website
Should not have
• no spirlay fonts or any thing scrolly. I want t professional IT website

```html
<!DOCTYPE html>
<html lang="en">
<head>
<meta charset="utf-8">
<title>Solvanta – Technology Advisor</title>
<link href="https://fonts.googleapis.com/css2?family=Exo+2:wght@400;600;700&family=Open+Sans:ital,wght@0,400;0,600;1,400&display=swap" rel="stylesheet">
<style>
:root{
  --green:#5fb13a;
  --green-dark:#3f9a35;
  --navy:#0f2f6b;
  --blue:#1d5fbf;
  --purple:#6a1b8a;
  --teal-title:#14485a;
  --text:#444;
  --muted:#666;
  --footer:#111;
  --white:#fff;
  --partner:#5a5a5a;
}
*{box-sizing:border-box;margin:0;padding:0}
html,body{width:1200px;height:3958px;overflow:hidden}
body{font-family:"Open Sans",Arial,sans-serif;color:var(--text);background:#fff;position:relative}
.heading{font-family:"Exo 2",Arial,sans-serif;font-weight:700;letter-spacing:.5px}
.btn{position:absolute;display:flex;align-items:center;justify-content:center;border-radius:30px;font-size:15px;font-weight:600;color:#fff;text-transform:uppercase}
.btn-solid{background:var(--green)}
.btn-ghost{border:2px solid #fff}
.placeholder{position:absolute}

/* header */
.site-header{position:absolute;top:0;left:0;width:1200px;height:92px;background:#fff}
.brand{position:absolute;display:flex;align-items:center;gap:10px;font-family:"Exo 2",sans-serif;font-weight:600}
.brand-dot{width:30px;height:30px;border-radius:50%;border:4px solid var(--green)}
.nav{position:absolute;left:400px;top:34px;display:flex;font-size:13px;color:#333}
.nav span{padding:0 24px;border-left:1px solid #999;line-height:18px}
.nav span:first-child{border-left:none;color:var(--purple);font-weight:600}

/* hero */
.hero{position:absolute;top:92px;left:0;width:1200px;height:610px}
.hero-photo{inset:0;background:linear-gradient(110deg,#0d1a2b 0%,#1d3447 45%,#3a4e5c 70%,#1b2731 100%)}
.hero-title{position:absolute;left:99px;top:180px;color:#fff;font-size:39px;line-height:49px}
.hero-title .light{font-weight:400}
.hero-dots{position:absolute;left:1145px;top:270px;display:flex;flex-direction:column;gap:7px}
.hero-dots i{width:10px;height:10px;border-radius:50%;background:#fff}
.hero-dots i:first-child{background:none;border:2px solid #fff}

/* about */
.section-title{position:absolute;font-size:34px;color:var(--navy)}
.about-art{left:98px;top:753px;width:402px;height:400px;border-radius:50%;background:radial-gradient(circle,#2c6fe0 0%,#1d3fb8 55%,#2a1a7a 100%)}
.about-text{position:absolute;left:581px;top:886px;width:525px;font-size:14px;line-height:22px;color:var(--text)}
.about-text p+p{margin-top:22px}

/* solutions */
.solutions{position:absolute;top:1295px;left:0;width:1200px;height:375px;display:flex;gap:2px;background:#fff}
.tile{position:relative;flex:1;overflow:hidden}
.tile-label{position:absolute;bottom:30px;left:0;right:0;text-align:center;color:#fff;font-size:22px}
.tile-1{background:linear-gradient(160deg,#1a2436,#3a4f6e 60%,#1b2333)}
.tile-2{background:linear-gradient(180deg,#2b1fa0,#4a1ea6 60%,#6a1d95)}
.tile-3{background:linear-gradient(160deg,#5f6b78,#2b3641 70%,#1e262f)}
.tile-4{background:linear-gradient(160deg,#1d2228,#4c565f 55%,#20262c)}
.tile-2 h3{position:absolute;top:86px;width:100%;text-align:center;color:#fff;font-size:22px}
.tile-2 p{position:absolute;top:122px;left:36px;right:36px;text-align:center;color:#e8e4ff;font-size:12px;line-height:22px}

/* experts */
.experts{position:absolute;top:1670px;left:0;width:1200px;height:552px;background:linear-gradient(120deg,#1a4fb8,#1e73d8 55%,#0d3d9c)}
.experts svg{position:absolute;left:0;top:0}
.experts-art{left:520px;top:0;width:680px;height:552px;background:radial-gradient(ellipse at 60% 45%,rgba(90,200,255,.55),rgba(30,100,210,0) 65%)}
.experts h2{position:absolute;left:100px;top:103px;color:#fff;font-size:26px}
.experts .lead{position:absolute;left:84px;top:167px;width:410px;color:#fff;font-size:14px;line-height:25px}
.check-list{position:absolute;list-style:none;color:#fff;font-size:14px;line-height:28px}
.check-list li{display:flex;align-items:center;gap:8px}
.check-list svg{position:static}

/* testimonials */
.testi-photo{left:202px;top:2390px;width:202px;height:202px;border-radius:50%;background:linear-gradient(160deg,#c9ccd2,#7a8088 60%,#2d3440)}
.quote-badge{position:absolute;left:360px;top:2408px;width:58px;height:58px;border-radius:50%;background:var(--purple);color:#fff;font-family:Georgia,serif;font-size:40px;font-weight:700;text-align:center;line-height:66px}
.testi-rule{position:absolute;left:446px;top:2390px;width:1px;height:200px;background:#ccc}
.testi-quote{position:absolute;left:473px;top:2418px;width:560px;font-style:italic;font-size:15.5px;line-height:32px;color:#666}
.testi-author{position:absolute;left:476px;top:2529px;font-size:14.5px;color:#333}
.testi-dots{position:absolute;left:480px;top:2577px;display:flex;gap:6px}
.testi-dots i{width:8px;height:8px;border-radius:50%;background:#444}
.testi-dots i.on{background:#2a9bd3}

/* why */
.why{position:absolute;top:2692px;left:0;width:1200px;height:519px;background:linear-gradient(110deg,#0b1f5e,#153f9a 50%,#1d5fc4)}
.why-art{left:0;top:0;width:620px;height:519px;background:radial-gradient(ellipse at 40% 50%,rgba(40,180,230,.45),rgba(120,30,120,.25) 45%,rgba(10,30,90,0) 75%)}
.why h2{position:absolute;left:670px;top:114px;color:#fff;font-size:31px}
.why-text{position:absolute;left:648px;top:187px;width:420px;color:#fff;font-size:14.5px;line-height:25px}
.why-text p+p{margin-top:25px}

/* partners */
.partners{position:absolute;top:3418px;left:200px;width:830px;display:flex;justify-content:space-between;align-items:center}
.partner{font-family:"Exo 2",sans-serif;font-weight:600;font-size:28px;line-height:34px;color:var(--partner)}

/* footer */
.site-footer{position:absolute;top:3602px;left:0;width:1200px;height:356px;background:var(--footer);color:#ddd}
.site-footer .brand{left:143px;top:56px;color:#fff;font-size:36px}
.foot-about{position:absolute;left:145px;top:132px;width:240px;font-size:11px;line-height:16px;color:#ccc}
.socials{position:absolute;left:146px;top:198px;display:flex;gap:22px}
.socials i{width:14px;height:14px;border-radius:50%;background:#fff}
.foot-col{position:absolute;top:70px}
.foot-col h4{font-family:"Exo 2",sans-serif;font-weight:600;font-size:19px;color:#fff;margin-bottom:12px}
.foot-col li{list-style:none;font-size:11.5px;line-height:23.5px;color:#ccc}
.contact-row{display:flex;gap:10px;align-items:flex-start;font-size:11.5px;line-height:15px;color:#ccc;margin-bottom:20px}
.foot-rule{position:absolute;left:133px;top:295px;width:920px;height:1px;background:#333}
.copyright{position:absolute;top:310px;width:1200px;text-align:center;font-size:11.5px;color:#ccc}
</style>
</head>
<body>

<header class="site-header">
  <div class="brand" style="left:98px;top:24px;font-size:34px;color:#111"><span class="brand-dot"></span>Solvanta</div>
  <nav class="nav"><span>HOME</span><span>ABOUT US</span><span>SERVICES</span><span>WHY SOLVANTA</span><span>TESTIMONIALS</span><span>CONTACT US</span></nav>
</header>

<section class="hero">
  <div class="placeholder hero-photo" role="img" aria-label="Low-angle photo of two engineers with a tablet in a server room"></div>
  <h1 class="hero-title heading"><span class="light">TECHNOLOGY ADVISOR</span><br>THAT HELPS TO<br>OPTIMIZE COSTS</h1>
  <div class="btn btn-solid" style="left:99px;top:351px;width:193px;height:52px;font-size:17px">Learn More</div>
  <div class="hero-dots"><i></i><i></i><i></i><i></i></div>
</section>

<section class="about">
  <div class="placeholder about-art" role="img" aria-label="Illustration of a cloud data center on a blue globe with colored rays"></div>
  <h2 class="section-title heading" style="left:593px;top:802px">ABOUT SOLVANTA</h2>
  <div class="about-text">
    <p>In a complex world of IT, Solvanta will assist you in optimizing IT spend. Our 20 plus years in the IT industry brings best of breed personnel from Data center, Managed Services, and Disaster Recovery, to help you get the best solutions for the best price. In a complex world of IT, let us help simplify.</p>
    <p>Aorta libero id ullamcorper nonummy nibh ligula pulvinar metus eget consectetuer augue nisi quis lacus Ut ac mi quis lacus mollis</p>
  </div>
  <div class="btn btn-solid" style="left:578px;top:1073px;width:173px;height:48px">Learn More</div>
</section>

<h2 class="section-title heading" style="left:507px;top:1213px">OUR SOLUTIONS</h2>
<section class="solutions">
  <div class="tile tile-1" role="img" aria-label="Photo of a hand touching a cloud interface"><span class="tile-label heading">CLOUD</span></div>
  <div class="tile tile-2">
    <h3 class="heading">DATA CENTER</h3>
    <p>Todays data centers are complex and have many moving parts. We help customers understand best of breed solutions for in house data center or outsourced data center decisions.</p>
    <div class="btn btn-ghost" style="left:74px;top:270px;width:152px;height:42px;font-size:13px">Learn More</div>
  </div>
  <div class="tile tile-3" role="img" aria-label="Photo of engineers with a laptop in a server room"><span class="tile-label heading">MANAGED SERVICES</span></div>
  <div class="tile tile-4" role="img" aria-label="Photo of a stressed man facing server racks"><span class="tile-label heading">DISASTER RECOVERY</span></div>
</section>

<section class="experts">
  <div class="placeholder experts-art" role="img" aria-label="Illustration of a cloud connected to a laptop and chips"></div>
  <svg width="600" height="552" viewBox="0 0 600 552"><defs><linearGradient id="g" x1="0" y1="0" x2="1" y2="1"><stop offset="0" stop-color="#4fae3b"/><stop offset="1" stop-color="#2f9a3a"/></linearGradient></defs><polygon points="0,0 415,0 595,275 412,552 0,552" fill="url(#g)"/></svg>
  <h2 class="heading">OUR EMPLOY EXPERTS</h2>
  <p class="lead">Aristique vel tellus Pellentesque nibh libero ultricies eu sagittis non mollis sed justo Praesent metus</p>
  <ul class="check-list" style="left:81px;top:238px">
    <li><svg width="15" height="15" viewBox="0 0 16 16"><circle cx="8" cy="8" r="8" fill="#fff"/><path d="M4.5 8.2l2.4 2.4 4.6-4.8" stroke="#3f9a35" stroke-width="2" fill="none"/></svg>IT including Cloud</li>
    <li><svg width="15" height="15" viewBox="0 0 16 16"><circle cx="8" cy="8" r="8" fill="#fff"/><path d="M4.5 8.2l2.4 2.4 4.6-4.8" stroke="#3f9a35" stroke-width="2" fill="none"/></svg>Mainframe</li>
    <li><svg width="15" height="15" viewBox="0 0 16 16"><circle cx="8" cy="8" r="8" fill="#fff"/><path d="M4.5 8.2l2.4 2.4 4.6-4.8" stroke="#3f9a35" stroke-width="2" fill="none"/></svg>ZR720/oFrame/TFrame</li>
    <li><svg width="15" height="15" viewBox="0 0 16 16"><circle cx="8" cy="8" r="8" fill="#fff"/><path d="M4.5 8.2l2.4 2.4 4.6-4.8" stroke="#3f9a35" stroke-width="2" fill="none"/></svg>Disaster Recovery</li>
    <li><svg width="15" height="15" viewBox="0 0 16 16"><circle cx="8" cy="8" r="8" fill="#fff"/><path d="M4.5 8.2l2.4 2.4 4.6-4.8" stroke="#3f9a35" stroke-width="2" fill="none"/></svg>IT optimization strategies</li>
  </ul>
  <ul class="check-list" style="left:332px;top:238px">
    <li><svg width="15" height="15" viewBox="0 0 16 16"><circle cx="8" cy="8" r="8" fill="#fff"/><path d="M4.5 8.2l2.4 2.4 4.6-4.8" stroke="#3f9a35" stroke-width="2" fill="none"/></svg>Colocation, Hybrid IT</li>
    <li><svg width="15" height="15" viewBox="0 0 16 16"><circle cx="8" cy="8" r="8" fill="#fff"/><path d="M4.5 8.2l2.4 2.4 4.6-4.8" stroke="#3f9a35" stroke-width="2" fill="none"/></svg>Migrations</li>
    <li><svg width="15" height="15" viewBox="0 0 16 16"><circle cx="8" cy="8" r="8" fill="#fff"/><path d="M4.5 8.2l2.4 2.4 4.6-4.8" stroke="#3f9a35" stroke-width="2" fill="none"/></svg>Networking</li>
    <li><svg width="15" height="15" viewBox="0 0 16 16"><circle cx="8" cy="8" r="8" fill="#fff"/><path d="M4.5 8.2l2.4 2.4 4.6-4.8" stroke="#3f9a35" stroke-width="2" fill="none"/></svg>Security</li>
  </ul>
  <div class="btn btn-ghost" style="left:73px;top:404px;width:162px;height:48px;font-size:14px">Learn More</div>
</section>

<section class="testimonials">
  <h2 class="section-title heading" style="left:496px;top:2301px;color:var(--teal-title)">TESTIMONIALS</h2>
  <div class="placeholder testi-photo" role="img" aria-label="Portrait photo of a smiling businessman in a suit"></div>
  <div class="quote-badge">“</div>
  <div class="testi-rule"></div>
  <p class="testi-quote">Morbi diam mauris viverra in gravida eu mattis in ante Morbi eget arcu Morbi porta libero id ullamcorper nonummy nibh ligula pulvinar metus eget consectetuer augue nisi quis lacus Ut ac mi quis lacus</p>
  <p class="testi-author">BY AUTHOR NAME</p>
  <div class="testi-dots"><i></i><i></i><i class="on"></i><i></i><i></i></div>
</section>

<section class="why">
  <div class="placeholder why-art" role="img" aria-label="Illustration of a glowing cloud computing network over devices"></div>
  <h2 class="heading">WHY SOLVANTA</h2>
  <div class="why-text">
    <p>Aorta libero id ullamcorper nonummy nibh ligula pulvinar metus eget consectetuer augue nisi quis lacus Ut ac mi quis lacus mollis aliquam Curabitur iaculis tempus eros</p>
    <p>Curabitur vel mi sit amet magna malesuada ultrices Ut nisi erat fermentum vel congue id euismod in elit</p>
  </div>
  <div class="btn btn-ghost" style="left:644px;top:375px;width:162px;height:48px;font-size:14px">Learn More</div>
</section>

<h2 class="section-title heading" style="left:516px;top:3278px">OUR PARTNERS</h2>
<div class="partners">
  <div class="partner">Quellbyte</div>
  <div class="partner">K&amp;L</div>
  <div class="partner">Corvanet</div>
  <div class="partner">Nimbara</div>
</div>

<footer class="site-footer">
  <div class="brand"><span class="brand-dot"></span>Solvanta</div>
  <p class="foot-about">Augiat in pede Fusce tellus Sed metus augue convallis et vehicula ut pulvinar eu ante Integer orci tellus tristique vitae consequat nec</p>
  <div class="socials" aria-label="Social links"><i></i><i></i><i></i><i></i></div>
  <div class="foot-col" style="left:462px"><h4>Quick Links</h4><ul><li>Home</li><li>Products</li><li>Capabilities</li><li>Leadership</li><li>Partners &amp; Results</li></ul></div>
  <div class="foot-col" style="left:653px"><h4>Resources</h4><ul><li>Business Development</li><li>News</li><li>Blogs</li><li>Contact us</li></ul></div>
  <div class="foot-col" style="left:856px"><h4>Contact Us</h4>
    <div class="contact-row"><svg width="14" height="16" viewBox="0 0 14 16"><path d="M7 1a5 5 0 0 0-5 5c0 4 5 9 5 9s5-5 5-9a5 5 0 0 0-5-5z" fill="none" stroke="#ccc" stroke-width="1.5"/><circle cx="7" cy="6" r="1.8" fill="#ccc"/></svg><span>48 Harlow Avenue #12<br>Austin 78701 TX</span></div>
    <div class="contact-row"><svg width="14" height="14" viewBox="0 0 14 14"><path d="M3 1l2.5 3-1.5 1.5c1 2 2.5 3.5 4.5 4.5L10 8.5l3 2.5-1.5 2C7 13 1 7 1 2.5z" fill="none" stroke="#ccc" stroke-width="1.3"/></svg><span>555.014.2290</span></div>
    <div class="contact-row"><svg width="15" height="12" viewBox="0 0 15 12"><rect x="1" y="1" width="13" height="10" fill="none" stroke="#ccc" stroke-width="1.3"/><path d="M1 1l6.5 5.5L14 1" fill="none" stroke="#ccc" stroke-width="1.3"/></svg><span>info@solvanta.example</span></div>
  </div>
  <div class="foot-rule"></div>
  <p class="copyright">© 2020 Company Name&nbsp; All right reserved</p>
</footer>

</body>
</html>
```